Brazilian-Italian food blogger looks for a yummy design for her blog

Ciao everyone! I am looking for a brand new design for my Wordpress food blog, MaRuPAN (marupan.net). The blog is about my deep love with food and with Bologna. I write particularly for the Brazilian crowd.
I talk about gastronomic curiosities of the town, delicious places and specialties that one can only find here. There are also many posts about my trips around Italy.
I would like the new design to be more sophisticated (or should I say professional?), but friendly at the same time.
If possible, I would like to keep its background very clean (if there are patters related to food, like the way it is now, even better), especially because I post many big colourful photos...
Also, since it is a personal blog, I would love if visitors could see a picture of mine and with a short description right at the homepage.
Thank you so much in advance.
Cheers,
Teresa.

Target Market(s)

Brazilian people interested in Italian culture and gastronomy.

Colors
fcca95

Requirements
Must have
• A neutral background that does not interfere with photos.
• My photo with a short description on the homepage.
Nice to have
• A background that has something to do with food.
Should not have
• It should not look like a girly blog.

```html
<!DOCTYPE html>
<html lang="pt">
<head>
<meta charset="utf-8">
<title>MaRuPAN – Minha declaração de amor ao comer bem e a Bologna</title>
<link href="https://fonts.googleapis.com/css2?family=Oswald:wght@400;500&family=Arimo:ital,wght@0,400;0,700;1,400&family=Open+Sans:ital,wght@1,400;1,600&display=swap" rel="stylesheet">
<style>
:root{
  --orange:#df6138;
  --orange-dark:#c8502b;
  --cream:#f7f3ea;
  --pattern:#e9e9e9;
  --pattern-2:#dcdcdc;
  --ink:#1f1f1f;
  --text:#5a5a5a;
  --muted:#8a8a8a;
  --rule:#e2dccd;
  --footer:#141414;
  --white:#ffffff;
}
*{box-sizing:border-box;margin:0;padding:0}
html,body{width:1200px;height:2491px;overflow:hidden}
body{position:relative;font-family:"Arimo",Arial,sans-serif;color:var(--text);background:var(--pattern)}
.backdrop{position:absolute;inset:0;background:linear-gradient(180deg,var(--pattern) 0%,var(--pattern-2) 50%,var(--pattern) 100%)}
a{color:var(--orange);text-decoration:none}

/* top bar */
.brand{position:absolute;left:129px;top:20px;font-family:"Oswald",sans-serif;font-size:22px;font-weight:500;color:var(--ink);letter-spacing:.5px}
.top-nav{position:absolute;left:208px;top:8px;width:377px;height:32px;background:var(--orange);border-radius:16px;display:flex;align-items:center;gap:24px;padding-left:30px}
.top-nav a{color:var(--white);font-size:10.5px}
.search{position:absolute;left:830px;top:33px;width:208px;height:32px;background:var(--white);border:1px solid #d6d6d6;font-size:11px;color:#666;padding:9px 8px}
.search svg{position:absolute;right:6px;top:9px}

/* main nav */
.main-nav{position:absolute;left:141px;top:118px;width:918px;height:63px;background:var(--orange);border-radius:30px;box-shadow:0 3px 4px rgba(0,0,0,.18);display:flex;align-items:center;padding-left:46px}
.main-nav a{font-family:"Open Sans",sans-serif;font-style:italic;font-size:16px;color:var(--white);margin-right:33px}
.main-nav .dot{position:absolute;top:28px;width:8px;height:8px;border-radius:50%;background:var(--white);opacity:.85}

/* slider */
.slider{position:absolute;left:191px;top:201px;width:822px;height:351px;border-radius:4px;box-shadow:0 2px 6px rgba(0,0,0,.25);
  background:linear-gradient(180deg,#5d7fc4 0%,#9fb6df 30%,#b46a45 55%,#8a3f28 80%,#5a2b1d 100%)}
.arrow{position:absolute;top:368px}

/* panel */
.panel{position:absolute;left:141px;top:577px;width:922px;height:1842px;background:var(--cream);box-shadow:0 0 6px rgba(0,0,0,.12)}

/* posts */
.post{position:absolute;left:162px;width:623px}
.post-title{font-family:"Oswald",sans-serif;font-weight:400;font-size:22px;color:var(--ink);line-height:1}
.post-meta{margin-top:14px;font-size:9.5px;color:#444;display:flex;align-items:center;gap:6px}
.post-meta svg{margin-left:14px}
.post-meta a{color:var(--orange)}
.post-body{margin-top:16px;display:flex;gap:21px}
.post-thumb{flex:none;width:170px;border:3px solid var(--white);box-shadow:0 0 2px rgba(0,0,0,.2)}
.post-text{font-size:11.5px;line-height:20.5px}
.post-text p{margin-bottom:10px}
.post-more{font-size:11.5px;line-height:20.5px}
.read-more{position:absolute;right:0;width:92px;height:22px;border-radius:11px;background:var(--orange);color:var(--white);font-size:11px;font-weight:700;text-align:center;line-height:22px}
.post-rule{position:absolute;left:162px;width:623px;height:1px;background:var(--rule)}
.pull-quote{position:absolute;left:0;width:245px;font-family:"Open Sans",sans-serif;font-style:italic;font-size:11px;line-height:19px;color:var(--muted);padding:20px 12px 0 22px}
.pull-quote .mark{position:absolute;font-family:Georgia,serif;font-size:46px;color:#cfc8b8;line-height:1}

.pagination{position:absolute;left:664px;top:2346px;display:flex;gap:5px}
.pagination span{height:25px;min-width:25px;border:1px solid #ccc;background:var(--white);font-size:11px;text-align:center;line-height:23px;padding:0 6px;color:#333}
.pagination .current{background:var(--orange-dark);border-color:var(--orange-dark);color:var(--white)}

/* sidebar */
.sidebar{position:absolute;left:814px;width:249px}
.widget-title{font-family:"Oswald",sans-serif;font-size:13.5px;color:var(--ink);padding-left:8px}
.widget-rule{position:absolute;left:814px;width:249px;height:3px;border-top:1px solid var(--rule);border-bottom:1px solid var(--rule)}
.about-photo{position:absolute;left:893px;top:633px;width:93px;height:94px;background:linear-gradient(160deg,#6b4a3c,#2b1e1a 60%,#8b6f5e)}
.about-name{position:absolute;left:814px;width:249px;top:744px;text-align:center;font-size:11px;font-weight:700;color:#333}
.about-desc{position:absolute;left:830px;width:217px;top:762px;text-align:center;font-size:11px;line-height:15px;color:#333}
.like-box{position:absolute;left:828px;top:868px;width:222px;height:222px;background:var(--white);border:1px solid #d8d8d8}
.like-box .page-thumb{position:absolute;left:5px;top:6px;width:50px;height:46px;background:linear-gradient(135deg,#a9845f,#5d4534)}
.like-box .page-name{position:absolute;left:62px;top:8px;font-size:11px;font-weight:700;color:#3b5998}
.like-box .like-btn{position:absolute;left:62px;top:26px;width:38px;height:16px;background:#4e69a2;border-radius:2px}
.like-box .count{position:absolute;left:6px;top:62px;font-size:9.5px;color:#555}
.fans{position:absolute;left:6px;top:90px;display:grid;grid-template-columns:repeat(5,40px);gap:3px}
.fans span{height:46px;background:#b7aea3}
.fans span:nth-child(2n){background:#8d8378}
.fans span:nth-child(3n){background:#c9bfb2}
.like-box .plugin{position:absolute;left:6px;bottom:8px;font-size:8.5px;color:#777}

.recent{position:absolute;left:822px;width:233px;font-size:11px;line-height:14px;color:#444}
.recent .date{position:absolute;left:0;top:0;width:76px;text-align:center}
.recent .day{font-family:"Oswald",sans-serif;font-size:26px;color:#333;line-height:30px}
.recent .month{font-size:10.5px;color:#333}
.recent .thumb{position:absolute;left:85px;top:0;width:50px;height:48px;border:2px solid var(--white)}
.recent .head{margin-left:148px;min-height:64px}
.recent .head b{font-weight:400;display:block;color:#333}
.recent .tail{margin-top:0}

.categories{position:absolute;left:824px;top:2041px;list-style:none;font-size:11.5px;color:#333}
.categories li{height:39px}
.categories li::before{content:"» "}

/* footer */
.footer{position:absolute;left:0;top:2433px;width:1200px;height:58px;background:var(--footer);color:var(--white);font-size:11px;text-align:center;padding-top:22px}
</style>
</head>
<body>
<div class="backdrop" role="img" aria-label="Repeating pattern of forks, knives and spoons in soft grey"></div>

<header>
  <div class="brand">MaRuPAN</div>
  <nav class="top-nav">
    <a>Home</a><a>O blog</a><a>Bella Bo</a><a>BUONI POSTI</a><a>Eu, Teresa</a>
  </nav>
  <div class="search">Search
    <svg width="12" height="12" viewBox="0 0 12 12"><circle cx="5" cy="5" r="3.5" fill="none" stroke="#333" stroke-width="1.5"/><line x1="7.5" y1="7.5" x2="11" y2="11" stroke="#333" stroke-width="1.5"/></svg>
  </div>
  <nav class="main-nav">
    <span class="dot" style="left:14px"></span>
    <a>Home</a><a>O blog</a><a>Bella Bo</a><a>BUONI POSTI</a><a>Eu, Teresa</a><a>FUORI CASA</a><a>LISTA DE RESTAURANTES</a><a>Contato</a>
    <span class="dot" style="right:14px"></span>
  </nav>
</header>

<section class="slider" role="img" aria-label="Photo of Bologna rooftops and medieval towers under a blue sky"></section>
<svg class="arrow" style="left:164px" width="14" height="20" viewBox="0 0 14 20"><path d="M11 2 3 10l8 8" fill="none" stroke="#d9412a" stroke-width="3"/></svg>
<svg class="arrow" style="left:1025px" width="14" height="20" viewBox="0 0 14 20"><path d="M3 2l8 8-8 8" fill="none" stroke="#d9412a" stroke-width="3"/></svg>

<main class="panel"></main>

<!-- Post 1 -->
<article class="post" style="top:597px">
  <h2 class="post-title">Dando de barato</h2>
  <div class="post-meta">September 16, 2014,
    <svg width="10" height="12" viewBox="0 0 10 12"><path d="M1 1h6l2 2v8H1z" fill="none" stroke="#999"/></svg><a>Pasta</a>
    <svg width="12" height="12" viewBox="0 0 12 12"><circle cx="6" cy="4" r="3" fill="#aaa"/><path d="M1 12c0-4 10-4 10 0" fill="#aaa"/></svg><a>No comments</a> | <a>Edit</a>
  </div>
  <div class="post-body">
    <div class="post-thumb" style="height:162px;background:radial-gradient(circle at 50% 50%,#f1c15a,#d88a2c 70%,#f4efe6)" role="img" aria-label="Plate of pasta shells"></div>
    <div class="post-text">
      <p>É inquietante como damos de barato certas coisas que, no fundo são excepcionais – e raras. A companhia de pessoas queridas, o litoral brasileiro, água-de-coco... Pequenas coisas que, ainda que muito especiais, por se tornarem corriqueiras nas nossas vidas, não damos o devido valor.</p>
      <p>Me dei conta que um desses exemplos é um dos restaurantes de que mais gosto aqui em Bologna, o <i>Sal Fino</i>.</p>
    </div>
  </div>
  <div class="post-more" style="margin-top:2px">
    <p>Bato ponto pelo menos uma vez por semana – já virou quase rotina – e por me sentir sempre em casa, por conhecer os chefs e os garçons, e, principalmente, porque comer bem ali é uma constância, deixei de perceber que a qualidade dos pratos do local é extraordinária, e muito difícil de se replicada.</p>
    <p style="margin-top:10px">O Sal Fino é um dos raros exemplos de cozinha meridional (i.e...</p>
  </div>
</article>
<a class="read-more" style="left:691px;top:920px">Read More</a>
<div class="post-rule" style="top:967px"></div>

<!-- Post 2 -->
<article class="post" style="top:1000px">
  <h2 class="post-title">Mortadella Bologna</h2>
  <div class="post-meta">September 16, 2014,
    <svg width="10" height="12" viewBox="0 0 10 12"><path d="M1 1h6l2 2v8H1z" fill="none" stroke="#999"/></svg><a>Uncategorized</a>
    <svg width="12" height="12" viewBox="0 0 12 12"><circle cx="6" cy="4" r="3" fill="#aaa"/><path d="M1 12c0-4 10-4 10 0" fill="#aaa"/></svg><a>No comments</a> | <a>Edit</a>
  </div>
  <div class="post-body">
    <div class="post-thumb" style="height:152px;background:linear-gradient(160deg,#d98c8c,#a24040 45%,#6f7a3a 80%)" role="img" aria-label="Mortadella and cured meats on a market counter"></div>
    <div class="post-text">
      <p>Em uma pequena ruazinha chamada Vicolo dei Limoni, bem no centro histórico de Bologna, há uma placa, redonda, com os seguintes dizeres:</p>
      <p>Em outras palavras, foi bem ali que a história do embutido cor-de-rosa mais querido do mundo se misturou à de Bologna, a ponto de receber o próprio nome da cidade, <i>“Mortadella Bologna”</i>.</p>
      <p>Os Salumai (ou Salumaio), mencionados na placa, eram os membros da cooperativa mais antiga de produtores de frios da região, responsáveis pela elaboração de mortadela e outros salumi desde o século XII.</p>
    </div>
  </div>
  <div style="position:relative;height:180px">
    <blockquote class="pull-quote" style="top:4px">
      <span class="mark" style="left:0;top:2px">“</span>
      “Esta casa era a sede, de 1242 a 1796, da arte dos Salumai, que controlavam a produção dos salumi Bolognesi, dos quais a excelente mortadela fez grande no mundo o mito de Bologna “la grassa” (“a gorda”)”.
      <span class="mark" style="right:10px;bottom:-38px">”</span>
    </blockquote>
    <p class="post-more" style="position:absolute;left:259px;top:4px">Sua história é peculiar: antes de s...</p>
  </div>
</article>
<a class="read-more" style="left:691px;top:1476px">Read More</a>
<div class="post-rule" style="top:1526px"></div>

<!-- Post 3 -->
<article class="post" style="top:1550px">
  <h2 class="post-title">Simplesmente pão e leite</h2>
  <div class="post-meta">September 16, 2014,
    <svg width="10" height="12" viewBox="0 0 10 12"><path d="M1 1h6l2 2v8H1z" fill="none" stroke="#999"/></svg><a>Sweets</a>
    <svg width="12" height="12" viewBox="0 0 12 12"><circle cx="6" cy="4" r="3" fill="#aaa"/><path d="M1 12c0-4 10-4 10 0" fill="#aaa"/></svg><a>No comments</a> | <a>Edit</a>
  </div>
  <div class="post-body">
    <div class="post-thumb" style="height:151px;background:linear-gradient(150deg,#e8d8b8,#b98546 50%,#6d4a2a)" role="img" aria-label="Sliced sweet bread with milk"></div>
    <div class="post-text">
      <p>No fim de semana passado, escapei (de novo) para a montanha, desta vez para as Dolomitas, no Trentino-Alto Adige. Essa é uma região muito particular da Itália, onde a primeira língua é o alemão, e, de tão organizada e precisa, qualquer italiano vindo de outro lugar se sente um peixe fora d'água.</p>
      <p>Mas, de jeito nenhum digo isso em modo depreciativo: é uma delícia rodar por estradas sem buracos, visitar lugares turísticos (como as trilhas da Marmolada, uma montanha perenemente coberta de neve, ou aquelas que levam até os 3.152m do Piz Alto) sem se perder no meio do caminho. Sem falar que é muito divertido ouvir as pessoas misturarem o alemão com o italiano sem perceber.</p>
    </div>
  </div>
  <div class="post-more">
    <p>Porém, confesso foram duas coisas muito simples que mais impressionaram: o pão e o iogurte.</p>
    <p style="margin-top:10px">Isso mesmo.</p>
  </div>
</article>
<a class="read-more" style="left:691px;top:1877px">Read More</a>
<div class="post-rule" style="top:1930px"></div>

<!-- Post 4 -->
<article class="post" style="top:1953px">
  <h2 class="post-title">Insalata di riso della Giulia</h2>
  <div class="post-meta">September 16, 2014,
    <svg width="10" height="12" viewBox="0 0 10 12"><path d="M1 1h6l2 2v8H1z" fill="none" stroke="#999"/></svg><a>Rise</a>
    <svg width="12" height="12" viewBox="0 0 12 12"><circle cx="6" cy="4" r="3" fill="#aaa"/><path d="M1 12c0-4 10-4 10 0" fill="#aaa"/></svg><a>No comments</a> | <a>Edit</a>
  </div>
  <div class="post-body">
    <div class="post-thumb" style="height:170px;background:radial-gradient(circle at 40% 45%,#f3d36a,#d9643a 40%,#6c8f3a 75%)" role="img" aria-label="Colourful rice salad in a bowl"></div>
    <div class="post-text">
      <p>Dizem aqui que toda menina italiana tem sua receita de insalata di riso. Sinceramente não sei quanto seja verdade e, confesso, receita minha mesmo só denisalata di farro (já mostrei aqui). Mas, para me garantir, peguei emprestado a receita da minha sogra e, como funciona tão bem, não pretendo mudar.</p>
      <p>A insalata di riso é muito comum nas mesas italianas, de norte a sul. Mesmo nas lojas que vendem comidas prontas, ela marca presença quase o ano todo.</p>
      <p>Mas o bacana mesmo é que não existe uma receita típica, em cada esquina ela tem uma cara diferente. A única coisa em comum é o fato de ser feita com arroz e essencialmente coisinhas que qualquer um compra já prontas no supermercado: atum, azeitona, ervilhas,</p>
    </div>
  </div>
  <p class="post-more" style="margin-top:-10px">queijo, conservas, presunto, salsicha, e por aí vai...</p>
</article>
<a class="read-more" style="left:691px;top:2252px">Read More</a>

<div class="pagination"><span class="current">1</span><span>2</span><span>Next »</span></div>

<!-- Sidebar -->
<aside>
  <h3 class="sidebar widget-title" style="top:602px">About</h3>
  <div class="about-photo" role="img" aria-label="Portrait photo of the author"></div>
  <p class="about-name">MaRuPAN</p>
  <p class="about-desc">Minha declaração de amor ao comer bem e a Bologna</p>
  <div class="widget-rule" style="top:812px"></div>

  <h3 class="sidebar widget-title" style="top:835px">Like the blog</h3>
  <div class="like-box">
    <div class="page-thumb" role="img" aria-label="Blog page thumbnail"></div>
    <span class="page-name">MaRuPAN</span>
    <span class="like-btn"></span>
    <span class="count">144 people like MaRuPAN.</span>
    <div class="fans" role="img" aria-label="Reader profile pictures">
      <span></span><span></span><span></span><span></span><span></span>
      <span></span><span></span><span></span><span></span><span></span>
    </div>
    <span class="plugin">Social plugin</span>
  </div>
  <div class="widget-rule" style="top:1110px"></div>

  <h3 class="sidebar widget-title" style="top:1130px">Recent Posts</h3>

  <div class="recent" style="top:1173px">
    <div class="date"><div class="day">16</div><div class="month">September</div></div>
    <div class="thumb" style="background:#e0a445" role="img" aria-label="Pasta thumbnail"></div>
    <p class="head"><b>Dando de barato</b>É inquietante como de me dei conta, que</p>
    <p class="tail">certas coisas que, no fundo são excepcionais – e raras...</p>
  </div>
  <div class="recent" style="top:1302px">
    <div class="date"><div class="day">16</div><div class="month">September</div></div>
    <div class="thumb" style="background:#b45252" role="img" aria-label="Mortadella thumbnail"></div>
    <p class="head"><b>Mortadella Bologna</b>Em uma pequena ruazinha</p>
    <p class="tail">chamada Vicolo dei Limoni, bem no centro histórico de Bologna, há uma placa, redonda, com os segui...</p>
  </div>
  <div class="recent" style="top:1428px">
    <div class="date"><div class="day">16</div><div class="month">September</div></div>
    <div class="thumb" style="background:#a87a4a" role="img" aria-label="Bread thumbnail"></div>
    <p class="head"><b>Simplesmente pão e leite</b>No fim de semana passado,</p>
    <p class="tail">escapei (de novo) para a montanha, desta vez para as Dolomitas, no Trentino-Alto Adige...</p>
  </div>
  <div class="recent" style="top:1578px">
    <div class="date"><div class="day">16</div><div class="month">September</div></div>
    <div class="thumb" style="background:#d98a44" role="img" aria-label="Rice salad thumbnail"></div>
    <p class="head"><b>Insalata di riso della Giulia</b>Dizem aqui que toda menina italiana tem</p>
    <p class="tail">sua receita de insalata di riso...</p>
  </div>
  <div class="recent" style="top:1696px">
    <div class="date"><div class="day">14</div><div class="month">September</div></div>
    <div class="thumb" style="background:#c79a6a" role="img" aria-label="Travel thumbnail"></div>
    <p class="head"><b>Saudades</b>Em uma visita zás-trás por São Paulo, me dei conta que,</p>
    <p class="tail">além de todo o mais, sinto realmente falta de algumas comidas "d...</p>
  </div>
  <div class="recent" style="top:1823px">
    <div class="date"><div class="day">13</div><div class="month">September</div></div>
    <div class="thumb" style="background:#c8a24c" role="img" aria-label="Mountain food thumbnail"></div>
    <p class="head"><b>Montanha mágica</b>Não sei se é mal de brasileiro, ou</p>
    <p class="tail">só meu mesmo, mas quando o calor de verdade (tipo mais de 32 graus) começa a pegar, o...</p>
  </div>
  <div class="widget-rule" style="top:1970px"></div>

  <h3 class="sidebar widget-title" style="top:1997px">Categories</h3>
  <ul class="categories">
    <li>Mortadella</li><li>Pasta</li><li>Rise</li><li>Sweets</li><li>Uncategorized</li>
  </ul>
  <div class="widget-rule" style="top:2238px"></div>
</aside>

<footer class="footer">Copyright © 2014 MaRuPAN</footer>
</body>
</html>
```